Maple Roster Business Card for recruitment company

We are looking for a Business Card Design that incorporates our personal details and our busines name and logo. We are a specialized search consultancy that recruit Property and Construction professionals.
We would like a business card that stands out and is appealing to the Construction and Property industry as well.

Target Market(s)

people in the construction and property industry

Contact Information for Business Card

Business Name and logo

Font styles to use
Serif

Colors
0094D4
00A9DD
6FCCEA
C7EBF8
E9F6FB

Requirements
Must have
• Business name and logo as well as contact details
Should not have
• No photos of us please

```html
<!DOCTYPE html>
<html lang="en">
<head>
<meta charset="utf-8">
<title>Maple Roster – Business Card</title>
<link rel="stylesheet" href="https://fonts.googleapis.com/css2?family=Cinzel:wght@400;600&family=Montserrat:wght@400&display=swap">
<style>
  :root {
    --backdrop: #d3d3d3;
    --paper: #ffffff;
    --ink-navy: #053a4e;
    --ink-text: #333333;
    --ink-light: #ffffff;
    --accent-blue: #0094d4;
    --accent-sky: #00a9dd;
    --accent-pale: #6fccea;
    --accent-mist: #c7ebf8;
    --shadow: rgba(0, 0, 0, 0.28);
  }
  * { margin: 0; padding: 0; box-sizing: border-box; }
  html, body {
    width: 900px;
    height: 1200px;
    overflow: hidden;
    background: var(--backdrop);
    font-family: "Montserrat", Arial, sans-serif;
  }
  .canvas { position: relative; width: 900px; height: 1200px; }

  .card {
    position: absolute;
    left: 79px;
    width: 743px;
    height: 440px;
    box-shadow: 0 6px 18px var(--shadow);
    overflow: hidden;
  }
  .card--front { top: 131px; background: var(--paper); border-bottom: 3px solid var(--accent-blue); }
  .card--back { top: 638px; background: var(--ink-navy); }

  .wordmark {
    position: absolute;
    left: 0; right: 0;
    display: flex;
    justify-content: center;
    align-items: center;
    gap: 16px;
    font-family: "Cinzel", Georgia, serif;
    font-weight: 400;
    font-size: 66px;
    letter-spacing: 2px;
    line-height: 1;
    white-space: nowrap;
  }
  .wordmark__dot {
    width: 24px; height: 24px;
    border-radius: 50%;
    background: var(--accent-blue);
    flex: none;
  }
  .card--front .wordmark { top: 64px; color: var(--ink-navy); }
  .card--back .wordmark { top: 188px; color: var(--ink-light); }

  .brand-mark-placeholder {
    position: absolute;
    left: 381px; top: 52px;
    width: 340px; height: 340px;
    border-radius: 50%;
    background: var(--accent-pale);
    opacity: 0.12;
  }

  .contact-band {
    position: absolute;
    left: 0; top: 201px;
    width: 100%; height: 146px;
    background: var(--ink-navy);
    color: var(--ink-light);
  }
  .person {
    position: absolute;
    right: 432px; top: 42px;
    text-align: right;
  }
  .person__name {
    font-family: "Cinzel", Georgia, serif;
    font-weight: 600;
    font-size: 25px;
    line-height: 1.2;
  }
  .person__role { font-weight: 400; font-size: 17px; margin-top: 4px; color: var(--accent-mist); }
  .divider {
    position: absolute;
    left: 353px; top: 40px;
    width: 2px; height: 70px;
    background: var(--accent-pale);
  }
  .contact-list {
    position: absolute;
    left: 388px; top: 36px;
    list-style: none;
    font-size: 16.5px;
    line-height: 26px;
  }
  .contact-list li { display: flex; align-items: center; }
  .contact-list svg { width: 15px; height: 15px; margin-right: 10px; fill: var(--accent-pale); }

  .address {
    position: absolute;
    left: 0; right: 0; top: 366px;
    text-align: center;
    font-size: 17px;
    color: var(--ink-text);
  }
</style>
</head>
<body>
<main class="canvas">
  <section class="card card--front" aria-label="Business card front">
    <h1 class="wordmark"><span class="wordmark__dot" aria-hidden="true"></span>Maple Roster</h1>
    <div class="contact-band">
      <div class="person">
        <p class="person__name">Dana Whitlow</p>
        <p class="person__role">Owner/ Designer</p>
      </div>
      <span class="divider"></span>
      <ul class="contact-list">
        <li>
          <svg viewBox="0 0 16 16" aria-hidden="true"><path d="M2 5c0-2 2-3 6-3s6 1 6 3v1h-3V4.5H5V6H2zM4 7h8l2 6H2zM8 8.5a2 2 0 1 0 0 4 2 2 0 0 0 0-4z"/></svg>
          (555) 204-7183
        </li>
        <li>
          <svg viewBox="0 0 16 16" aria-hidden="true"><path d="M1 4h14v1L8 9 1 5zM1 6.5l7 4 7-4V13H1z"/></svg>
          info@mapleroster.com
        </li>
        <li>
          <svg viewBox="0 0 16 16" aria-hidden="true"><path d="M8 1a7 7 0 1 0 0 14A7 7 0 0 0 8 1zm-1 2.5 1.5 1-1 1.5 2 1 .5 2-2 1-.5 2.5L6 10l-1-2-2-.5 1-2.5zM11 4l1.5 2-1 1-1.5-1z"/></svg>
          www.mapleroster.com
        </li>
      </ul>
    </div>
    <p class="address">72 Harbor Lane, Fairview Bay, CA 90210</p>
  </section>

  <section class="card card--back" aria-label="Business card back">
    <div class="brand-mark-placeholder" role="img" aria-label="Large faint brand mark placeholder"></div>
    <h2 class="wordmark">Maple Roster</h2>
  </section>
</main>
</body>
</html>
```